PLUMA Project Roll Up Banner 85x200 cm (1:10, 1200 dpi)

PLUMA is a EU-funded project to promote female entrepreneurship networks. The project is developed by 9 partners from 7 different countries.
The banner is to be used throughout the project in exhibitions, conferences, roundtables, etc.
It has to include the following graphic elements, which cannot be modified beyond scaling:
- PLUMA logo
- EU logo (cannot be modified in any way, and cannot have any kind of background, but pure white).
- 9 partners logos
- Facebook link (with logo)
- LinkedIn link (with logo)
- Project's website (www.pluma-circle.example)
The text to be included:
Pioneering Ladies Undertaking Market Advances
PLUMA: Contributes to the strengthening of the links between women entrepreneurs and the mainstream of new technologies, educational, and training practices offered all over Europe.
GOOD PRACTICES: Compilation of EU projects promoting female entrepreneurship and ICT systems for learning, supporting, and training women entrepreneurs.
NETWORK: Strengthening of linkages between EU women entrepreneurs, project managers, learning communities, multipliers, and society to encourage a knowledge-sharing environment through the creation of the PLUMA circle.
ONE-STOP SHOP: Development of a multi-lingual EU online platform, where valuable an innovative EU learning opportunities can be found and accessed at one single place, as well as fostering new business opportunities by a Virtual Market.
The banner has to be attractive the modern female entrepreneur. It has to be easy to read, and present a fresh and exciting identity.
The banner has to include 5 additional centimetres on the top, and 10 on the bottom.
The last partner logo has been uploaded now.
Female entrepreneurs
Higher Educational Institutions
Government Female Representatives
Environment

```html
<!DOCTYPE html>
<html lang="en">
<head>
<meta charset="utf-8">
<title>PLUMA Roll Up Banner</title>
<link rel="stylesheet" href="https://fonts.googleapis.com/css2?family=Jura:wght@400;500&family=Open+Sans:wght@400;600&display=swap">
<style>
  :root {
    --teal: #3fdcc4;
    --teal-deep: #2fc9b1;
    --white: #ffffff;
    --ink: #333a40;
    --grey-line: #b9c0c4;
    --brand-blue: #3b3f9e;
    --photo-low: #5d6168;
  }
  * { margin: 0; padding: 0; box-sizing: border-box; }
  html, body { width: 1200px; height: 3033px; overflow: hidden; background: var(--white); }
  .banner { position: relative; width: 1200px; height: 3033px; background: var(--teal); font-family: "Open Sans", Arial, sans-serif; color: var(--white); overflow: hidden; }

  .hero-photo {
    position: absolute; left: 0; top: 71px; width: 1200px; height: 1300px;
    background:
      radial-gradient(ellipse 300px 560px at 620px 640px, var(--photo-low), transparent 70%),
      linear-gradient(90deg, #b8bec3 0%, #e8ecee 25%, #cfd4d8 55%, #6f757c 80%, #4f555c 100%);
  }
  .hero-fade {
    position: absolute; left: 0; top: 1100px; width: 1200px; height: 271px;
    background: linear-gradient(180deg, rgba(255,255,255,0) 0%, #ffffff 100%);
  }
  .brand-strip {
    position: absolute; left: 0; top: 1371px; width: 1200px; height: 149px;
    background: linear-gradient(90deg, #ffffff 0%, #ffffff 45%, var(--teal) 100%);
  }

  .brand-mark { position: absolute; left: 90px; top: 1330px; display: flex; align-items: center; gap: 26px; }
  .brand-mark .dot { width: 70px; height: 70px; border-radius: 50%; background: var(--brand-blue); }
  .brand-mark .name { font-family: "Jura", sans-serif; font-weight: 500; font-size: 104px; letter-spacing: 6px; color: var(--brand-blue); line-height: 1; }

  .headline {
    position: absolute; left: 40px; top: 1560px; width: 1120px;
    font-family: "Jura", sans-serif; font-weight: 500; font-size: 66px; line-height: 1.15;
    text-align: center; color: var(--white);
  }

  .pillar { position: absolute; left: 46px; width: 1100px; display: flex; align-items: center; }
  .pillar-label { width: 268px; flex: none; font-family: "Jura", sans-serif; font-weight: 500; font-size: 46px; line-height: 1.05; text-transform: uppercase; }
  .pillar-text { flex: 1; font-size: 28px; line-height: 1.3; }
  .pillar.intro { top: 1803px; }
  .pillar.practices { top: 1975px; }
  .pillar.network { top: 2140px; }
  .pillar.shop { top: 2355px; }

  .partners { position: absolute; left: 0; top: 2562px; width: 1200px; height: 218px; background: var(--white); padding: 14px 24px; display: grid; grid-template-rows: 1fr 1fr; row-gap: 10px; }
  .partner-row { display: grid; grid-template-columns: repeat(5, 1fr); align-items: center; }
  .partner { display: flex; align-items: center; gap: 10px; padding: 0 12px; height: 80px; font-size: 21px; line-height: 1.15; font-weight: 600; color: var(--ink); border-left: 2px solid var(--grey-line); }
  .partner:first-child { border-left: none; padding-left: 0; }
  .partner .chip { flex: none; width: 24px; height: 24px; background: var(--teal-deep); }
  .partner .chip.round { border-radius: 50%; background: var(--brand-blue); }

  .contact-bar { position: absolute; left: 0; top: 2795px; width: 1200px; height: 86px; background: var(--white); }
  .contact { position: absolute; top: 0; height: 86px; display: flex; align-items: center; gap: 16px; font-size: 27px; color: var(--ink); white-space: nowrap; }
  .contact.social { left: 44px; }
  .contact.web { left: 296px; }
  .contact.group { left: 745px; }
  .contact .chip { width: 34px; height: 34px; background: var(--brand-blue); }
</style>
</head>
<body>
<main class="banner">
  <div class="hero-photo" role="img" aria-label="Portrait of a smiling young businesswoman in a grey cardigan and white scarf standing in front of modern office buildings"></div>
  <div class="hero-fade"></div>
  <div class="brand-strip"></div>

  <div class="brand-mark">
    <span class="dot"></span>
    <span class="name">PLUMA</span>
  </div>

  <h1 class="headline">Pioneering Ladies Undertaking<br>Market Advances</h1>

  <section class="pillar intro">
    <div class="pillar-label">PLUMA</div>
    <p class="pillar-text">Contributes to the strengthening of the links between women entrepreneurs and the mainstream of new technologies, educational, and training practices offered all over Europe.</p>
  </section>

  <section class="pillar practices">
    <div class="pillar-label">Good<br>Practices</div>
    <p class="pillar-text">Compilation of EU projects promoting female<br>entrepreneurship and ICT systems for learning,<br>supporting, and training women entrepreneurs.</p>
  </section>

  <section class="pillar network">
    <div class="pillar-label">Network</div>
    <p class="pillar-text">Strengthening of linkages between EU women entrepreneurs, project managers, learning communities, multipliers, and society to encourage a knowledge-sharing environment through the creation of the PLUMA circle.</p>
  </section>

  <section class="pillar shop">
    <div class="pillar-label">One-Stop<br>Shop</div>
    <p class="pillar-text">Development of a multi-lingual EU online platform, where valuable an innovative EU learning opportunities can be found and accessed at one single place, as well as fostering new business opportunities by a Virtual Market.</p>
  </section>

  <section class="partners" aria-label="Project partners">
    <div class="partner-row">
      <span class="partner"><span class="chip"></span>Orbita Sociale</span>
      <span class="partner"><span class="chip"></span>Norden Hogeschool</span>
      <span class="partner"><span class="chip"></span>edulink.example</span>
      <span class="partner"><span class="chip"></span>Vestby University</span>
      <span class="partner"><span class="chip"></span>Marmara Danışmanlık</span>
    </div>
    <div class="partner-row">
      <span class="partner"><span class="chip"></span>Sentiero Sviluppo</span>
      <span class="partner"><span class="chip"></span>FH Steinfeld</span>
      <span class="partner"><span class="chip"></span>tessera</span>
      <span class="partner"><span class="chip"></span>lumen consultancy</span>
      <span class="partner"><span class="chip round"></span>Lifelong Learning Scheme</span>
    </div>
  </section>

  <footer class="contact-bar">
    <span class="contact social"><span class="chip"></span>/pluma.circle</span>
    <span class="contact web">
      <svg width="34" height="34" viewBox="0 0 34 34" aria-hidden="true">
        <g fill="none" stroke="#3b3f9e" stroke-width="2.5">
          <circle cx="17" cy="17" r="14"/>
          <ellipse cx="17" cy="17" rx="6" ry="14"/>
          <line x1="3" y1="17" x2="31" y2="17"/>
          <line x1="17" y1="3" x2="17" y2="31"/>
        </g>
      </svg>
      www.pluma-circle.example
    </span>
    <span class="contact group"><span class="chip"></span>/groups/PLUMA-4720316</span>
  </footer>
</main>
</body>
</html>
```